Harborline Outpost Registry needs a web design

We are launching a new website and need a web design. The website is going to list every military base and installment around the world with information on each base such as a description of the base, the history of the base, contact information at the base, address, lat/long of the base, and any other relevant information including images of the base. We need a home page with navigation menu and the design of the military base page so that every military base page is formatted the same for the referenced information. We have included an example of the content that may be found on the base page(s). We are also going to have the information available in spanish.

We also wanted to mention we will be building this website in wordpress.

We also wanted to note that in the format of each base page, we will have a frequently asked questions section with answers.

```html
<!DOCTYPE html>
<html lang="en">
<head>
<meta charset="utf-8">
<title>Harborline Outpost Registry</title>
<link rel="stylesheet" href="https://fonts.googleapis.com/css2?family=Nunito+Sans:wght@400;600;700;800;900&family=Playfair+Display:wght@700&display=swap">
<style>
:root{
  --red:#b30000;
  --green:#0b5a26;
  --green-dark:#064a1e;
  --ink:#111111;
  --text:#3a3a3a;
  --muted:#555555;
  --soft:#f4f2f2;
  --blog-bg:#f2f1ef;
  --white:#ffffff;
  --footer:#0b0b0b;
  --line:#e4e2e2;
}
*{box-sizing:border-box;margin:0;padding:0}
html,body{width:1200px;height:3011px;overflow:hidden}
body{font-family:"Nunito Sans",Arial,sans-serif;color:var(--text);background:var(--white);position:relative}
.container{width:936px;margin:0 auto;position:relative}

/* Header */
.site-header{height:84px;display:flex;align-items:center}
.site-header .container{display:flex;align-items:center;justify-content:space-between}
.brand{font-family:"Playfair Display",Georgia,serif;font-weight:700;font-size:22px;color:var(--ink);white-space:nowrap}
.main-nav{display:flex;align-items:center;gap:26px;font-size:13.5px;color:#222;letter-spacing:.2px}
.main-nav .active{background:var(--red);color:var(--white);padding:6px 8px}
.lang{display:flex;align-items:center;gap:5px;font-size:13.5px}

/* Hero */
.hero{position:relative;height:492px;overflow:hidden}
.hero-art{position:absolute;inset:0;background:
  radial-gradient(ellipse at 62% 25%,#3a4a66 0%,rgba(30,38,58,0) 55%),
  linear-gradient(180deg,#1c2436 0%,#24304a 45%,#3b2a36 75%,#6a2a34 100%)}
.hero-shade{position:absolute;inset:0;background:linear-gradient(90deg,rgba(0,0,0,.35),rgba(0,0,0,.05) 50%,rgba(0,0,0,.3))}
.hero-title{position:absolute;top:276px;left:0;right:0;text-align:center;color:var(--white);font-weight:900;font-size:39px;letter-spacing:.3px}
.search{position:absolute;left:298px;top:346px;width:604px;height:53px;background:var(--white);display:flex;align-items:center;justify-content:space-between;padding:0 8px 0 20px}
.search span{font-size:14px;color:#333}
.search-btn{width:40px;height:40px;border-radius:50%;background:var(--green);display:flex;align-items:center;justify-content:center}

/* Section titles */
.section-title{text-align:center;font-weight:900;font-size:24px;color:var(--ink)}
.rule{width:46px;height:2px;background:var(--ink);margin:16px auto 0}

/* Military base grid */
.bases{padding:40px 0 0;height:444px}
.base-grid{display:grid;grid-template-columns:repeat(4,223px);gap:15px;margin-top:40px}
.base-img{height:171px}
.card-title{font-weight:800;font-size:13.2px;line-height:1.35;color:var(--green)}
.base-card .card-title{margin-top:14px}
.meta{font-size:13px;line-height:1.4;color:var(--muted);margin-top:10px}

/* Featured */
.featured{background:var(--soft);height:736px;padding-top:42px}
.featured-head{display:flex;justify-content:space-between;align-items:flex-start}
.featured-head h2{font-weight:900;font-size:24px;color:var(--ink)}
.featured-head .rule{margin:16px 0 0}
.btn-green{background:var(--green-dark);color:var(--white);font-weight:800;font-size:14px;padding:0 15px;height:34px;display:flex;align-items:center;margin-top:3px}
.listing-grid{display:grid;grid-template-columns:458px 458px;column-gap:20px;row-gap:14px;margin-top:36px}
.listing{background:var(--white);height:179px;display:flex;padding:9px 10px}
.listing-img{width:144px;height:160px;flex:none}
.listing-body{padding:14px 0 0 29px}
.listing .meta{margin-top:12px;padding-left:2px;line-height:1.55}
.btn-red{display:inline-block;background:var(--red);color:var(--white);font-weight:800;font-size:11px;padding:7px 12px;letter-spacing:.2px}
.listing .btn-red{margin-top:12px;margin-left:2px}

/* Reviews */
.reviews{height:474px;padding-top:44px;position:relative}
.review-grid{display:grid;grid-template-columns:repeat(3,300px);gap:18px;margin-top:40px}
.review{height:285px;border:1px solid var(--line);box-shadow:0 4px 14px rgba(0,0,0,.06);padding:36px 22px 0 20px}
.review-top{display:flex;align-items:center;gap:10px}
.quote{font-family:Georgia,serif;font-size:34px;line-height:1;color:var(--green);font-style:italic;height:22px}
.stars{color:var(--red);font-size:14px;letter-spacing:1px}
.review p{font-size:14.6px;line-height:1.48;color:#444;margin:12px 0 0 14px}
.reviewer{color:var(--green);font-size:14.5px;margin:12px 0 0 14px;letter-spacing:.3px}
.arrow{position:absolute;top:220px}
.arrow.prev{left:74px}
.arrow.next{left:1104px}

/* Blog */
.blog{background:var(--blog-bg);height:606px;padding-top:42px}
.blog .rule{background:var(--green)}
.blog-grid{display:grid;grid-template-columns:repeat(3,294px);gap:26px;margin-top:34px}
.post{background:var(--white);height:432px;border:1px solid var(--line)}
.post-img{height:193px}
.post-body{padding:24px 26px 0}
.post h3{font-weight:800;font-size:20px;line-height:1.2;color:var(--green)}
.post p{font-size:12.6px;line-height:1.28;color:#444;margin-top:14px}
.post .btn-red{margin-top:16px;margin-left:3px;padding:8px 13px}

/* Footer */
.site-footer{background:var(--footer);height:175px;color:var(--white)}
.footer-top{display:flex;justify-content:space-between;align-items:center;height:98px;border-bottom:1px solid #2a2a2a}
.footer-top .brand{color:var(--white)}
.footer-nav{display:flex;gap:30px;font-size:13.5px}
.copyright{text-align:center;font-size:11px;padding-top:30px}
</style>
</head>
<body>

<header class="site-header">
  <div class="container">
    <div class="brand">Harborline Outpost Registry</div>
    <nav class="main-nav">
      <span class="active">HOME</span>
      <span>ABOUT US</span>
      <span>SERVICES</span>
      <span>BASE DIRECTORY</span>
      <span>BLOG</span>
      <span>CONTACT US</span>
      <span class="lang">
        <svg width="20" height="20" viewBox="0 0 20 20" fill="none" stroke="#444" stroke-width="1.2"><circle cx="10" cy="10" r="8.5"/><ellipse cx="10" cy="10" rx="3.8" ry="8.5"/><line x1="1.5" y1="10" x2="18.5" y2="10"/><line x1="3" y1="5.5" x2="17" y2="5.5"/><line x1="3" y1="14.5" x2="17" y2="14.5"/></svg>
        <svg width="9" height="6" viewBox="0 0 9 6"><path d="M0 0h9L4.5 6z" fill="#222"/></svg>
        En
      </span>
    </nav>
  </div>
</header>

<section class="hero">
  <div class="hero-art" role="img" aria-label="Armed soldiers with helmets and a ballistic shield in front of a waving national flag"></div>
  <div class="hero-shade"></div>
  <h1 class="hero-title">HARBORLINE OUTPOST REGISTRY</h1>
  <div class="search">
    <span>SEARCH FOR A BASE</span>
    <div class="search-btn">
      <svg width="20" height="20" viewBox="0 0 20 20" fill="none" stroke="#fff" stroke-width="2.4" stroke-linecap="round"><circle cx="8.5" cy="8.5" r="6"/><line x1="13" y1="13" x2="18" y2="18"/></svg>
    </div>
  </div>
</section>

<section class="bases">
  <div class="container">
    <h2 class="section-title">MILITARY BASE</h2>
    <div class="rule"></div>
    <div class="base-grid">
      <article class="base-card">
        <div class="base-img" role="img" aria-label="Drone flying over desert hangars beneath mountains" style="background:linear-gradient(180deg,#a9b9cf 0%,#8c879a 45%,#7a6f6a 75%,#b9a88a 100%)"></div>
        <h3 class="card-title">Cedar Ridge Outpost: History, Facilities, and Support Services</h3>
        <p class="meta">Cedar Ridge, North Vale, Eastland<br>Number: (555) 018-2247</p>
      </article>
      <article class="base-card">
        <div class="base-img" role="img" aria-label="Troops advancing across a dusty field with smoke behind" style="background:linear-gradient(180deg,#b9b6ab 0%,#8f8a7c 50%,#5a5548 100%)"></div>
        <h3 class="card-title">Cedar Ridge Outpost: History, Facilities, and Support Services</h3>
        <p class="meta">Cedar Ridge, North Vale, Eastland<br>Number: (555) 018-2247</p>
      </article>
      <article class="base-card">
        <div class="base-img" role="img" aria-label="Aerial view of rows of tents on a desert camp" style="background:linear-gradient(135deg,#7d7a74 0%,#9a948a 50%,#a4835f 100%)"></div>
        <h3 class="card-title">Cedar Ridge Outpost: History, Facilities, and Support Services</h3>
        <p class="meta">Cedar Ridge, North Vale, Eastland<br>Number: (555) 018-2247</p>
      </article>
      <article class="base-card">
        <div class="base-img" role="img" aria-label="Aerial view of a walled base compound among trees" style="background:linear-gradient(135deg,#6f7a52 0%,#9c9484 50%,#5d6a40 100%)"></div>
        <h3 class="card-title">Cedar Ridge Outpost: History, Facilities, and Support Services</h3>
        <p class="meta">Cedar Ridge, North Vale, Eastland<br>Number: (555) 018-2247</p>
      </article>
    </div>
  </div>
</section>

<section class="featured">
  <div class="container">
    <div class="featured-head">
      <div>
        <h2>FEATURED BASE LISTINGS</h2>
        <div class="rule"></div>
      </div>
      <span class="btn-green">VIEW ALL LISTINGS</span>
    </div>
    <div class="listing-grid">
      <article class="listing">
        <div class="listing-img" role="img" aria-label="Desert outpost with vehicles and fencing" style="background:linear-gradient(180deg,#b29c82 0%,#9e8c76 50%,#7c7566 100%)"></div>
        <div class="listing-body">
          <h3 class="card-title">Cedar Ridge Outpost: History,<br>Facilities, and Support Services</h3>
          <p class="meta">Cedar Ridge, North Vale, Eastland<br>Number: (555) 018-2247</p>
          <span class="btn-red">READ MORE</span>
        </div>
      </article>
      <article class="listing">
        <div class="listing-img" role="img" aria-label="Aerial view of barracks blocks on green land" style="background:linear-gradient(180deg,#7c8f62 0%,#6a6f6c 50%,#4f5a44 100%)"></div>
        <div class="listing-body">
          <h3 class="card-title">Cedar Ridge Outpost: History,<br>Facilities, and Support Services</h3>
          <p class="meta">Cedar Ridge, North Vale, Eastland<br>Number: (555) 018-2247</p>
          <span class="btn-red">READ MORE</span>
        </div>
      </article>
      <article class="listing">
        <div class="listing-img" role="img" aria-label="Aerial view of a sand-coloured fortified complex" style="background:linear-gradient(135deg,#d2bd96 0%,#b49a74 55%,#8e7a60 100%)"></div>
        <div class="listing-body">
          <h3 class="card-title">Cedar Ridge Outpost: History,<br>Facilities, and Support Services</h3>
          <p class="meta">Cedar Ridge, North Vale, Eastland<br>Number: (555) 018-2247</p>
          <span class="btn-red">READ MORE</span>
        </div>
      </article>
      <article class="listing">
        <div class="listing-img" role="img" aria-label="Aircraft parked on a grass airfield" style="background:linear-gradient(180deg,#6f8450 0%,#627545 60%,#7b8062 100%)"></div>
        <div class="listing-body">
          <h3 class="card-title">Cedar Ridge Outpost: History,<br>Facilities, and Support Services</h3>
          <p class="meta">Cedar Ridge, North Vale, Eastland<br>Number: (555) 018-2247</p>
          <span class="btn-red">READ MORE</span>
        </div>
      </article>
      <article class="listing">
        <div class="listing-img" role="img" aria-label="Aerial view of a large five-sided headquarters building" style="background:linear-gradient(135deg,#5e6d4c 0%,#8a8a80 50%,#566446 100%)"></div>
        <div class="listing-body">
          <h3 class="card-title">Cedar Ridge Outpost: History,<br>Facilities, and Support Services</h3>
          <p class="meta">Cedar Ridge, North Vale, Eastland<br>Number: (555) 018-2247</p>
          <span class="btn-red">READ MORE</span>
        </div>
      </article>
      <article class="listing">
        <div class="listing-img" role="img" aria-label="Green field tents under a blue sky" style="background:linear-gradient(180deg,#4f88c8 0%,#8db3d8 35%,#5c6a3a 60%,#6f8046 100%)"></div>
        <div class="listing-body">
          <h3 class="card-title">Cedar Ridge Outpost: History,<br>Facilities, and Support Services</h3>
          <p class="meta">Cedar Ridge, North Vale, Eastland<br>Number: (555) 018-2247</p>
          <span class="btn-red">READ MORE</span>
        </div>
      </article>
    </div>
  </div>
</section>

<section class="reviews">
  <div class="container">
    <h2 class="section-title">REVIEWS</h2>
    <div class="rule"></div>
    <div class="review-grid">
      <article class="review">
        <div class="review-top"><span class="quote">“</span><span class="stars">★★★★★</span></div>
        <p>Sed ut perspiciatis unde omnis iste natus error sit voluptatem accus antium doloremque laudantium, totam rem ape riam, eaque ipsa quae ab illo inventore veritatis et quasi architecto beatae vitae dicta sunt explicabo.</p>
        <div class="reviewer">MARLOW</div>
      </article>
      <article class="review">
        <div class="review-top"><span class="quote">“</span><span class="stars">★★★★★</span></div>
        <p>Sed ut perspiciatis unde omnis iste natus error sit voluptatem accus antium doloremque laudantium, totam rem ape riam, eaque ipsa quae ab illo inventore veritatis et quasi architecto beatae vitae dicta sunt explicabo.</p>
        <div class="reviewer">MARLOW</div>
      </article>
      <article class="review">
        <div class="review-top"><span class="quote">“</span><span class="stars">★★★★★</span></div>
        <p>Sed ut perspiciatis unde omnis iste natus error sit voluptatem accus antium doloremque laudantium, totam rem ape riam, eaque ipsa quae ab illo inventore veritatis et quasi architecto beatae vitae dicta sunt explicabo.</p>
        <div class="reviewer">MARLOW</div>
      </article>
    </div>
  </div>
  <svg class="arrow prev" width="18" height="30" viewBox="0 0 18 30" fill="none" stroke="#222" stroke-width="2"><polyline points="15,2 3,15 15,28"/></svg>
  <svg class="arrow next" width="18" height="30" viewBox="0 0 18 30" fill="none" stroke="#222" stroke-width="2"><polyline points="3,2 15,15 3,28"/></svg>
</section>

<section class="blog">
  <div class="container">
    <h2 class="section-title" style="font-size:28px">LATEST BLOG</h2>
    <div class="rule"></div>
    <div class="blog-grid">
      <article class="post">
        <div class="post-img" role="img" aria-label="Aerial evening view of a lit base complex among trees" style="background:linear-gradient(135deg,#3e4a32 0%,#6b6450 50%,#2f3a28 100%)"></div>
        <div class="post-body">
          <h3>Sed ut perspiciatis unde omnis iste natus error sit voluptatem</h3>
          <p>At vero eos et accusamus et iusto odio dignissimos ducimus qui blanditiis praesentium voluptatum deleniti atque corrup.</p>
          <span class="btn-red">READ MORE</span>
        </div>
      </article>
      <article class="post">
        <div class="post-img" role="img" aria-label="Aircraft displayed on a grass airfield beside hangars" style="background:linear-gradient(135deg,#6f8450 0%,#7a8a66 55%,#5e7044 100%)"></div>
        <div class="post-body">
          <h3>Sed ut perspiciatis unde omnis iste natus error sit voluptatem</h3>
          <p>At vero eos et accusamus et iusto odio dignissimos ducimus qui blanditiis praesentium voluptatum deleniti atque corrup.</p>
          <span class="btn-red">READ MORE</span>
        </div>
      </article>
      <article class="post">
        <div class="post-img" role="img" aria-label="Armoured vehicles and troops on a dusty plain" style="background:linear-gradient(180deg,#5a5245 0%,#8a7a62 55%,#6e604c 100%)"></div>
        <div class="post-body">
          <h3>Sed ut perspiciatis unde omnis iste natus error sit voluptatem</h3>
          <p>At vero eos et accusamus et iusto odio dignissimos ducimus qui blanditiis praesentium voluptatum deleniti atque corrup.</p>
          <span class="btn-red">READ MORE</span>
        </div>
      </article>
    </div>
  </div>
</section>

<footer class="site-footer">
  <div class="container">
    <div class="footer-top">
      <div class="brand">Harborline Outpost Registry</div>
      <nav class="footer-nav">
        <span>HOME</span><span>ABOUT US</span><span>SERVICES</span><span>BASE DIRECTORY</span><span>BLOG</span><span>CONTACT US</span>
      </nav>
    </div>
    <p class="copyright">Copyright © 2023 All Rights Reserved</p>
  </div>
</footer>

</body>
</html>
```